To design a brand identity that is simple and creative with 'Corvane' as the brand name, I like modern simple fonts like helvetica neue, I want to print both sides of the card, I am open to dark front and white back, but the design needs to transfer well to letter heads and email signatures, I am looking for sophisticated and elegant, but open minded about clever and off the wall, I do not do 'boring' Corvane Ventures is the mother company for a small group, specialising in Management & consulting, Software development and construction, we have a high level of integrity, we are transparent and accountable for what we do. my images are provided as a guide only, Im not expecting them to be just copied, Im looking for a creator and passionate thinker, who will put life into their work.

Target Market(s)

usually business minded people who are looking for something different in me, such as leadership, confidence and focus with thinking that is per haps a little outside the box..

Industry/Entity Type

Construction

Requirements
Must have
• clean, minmalistic
Nice to have
• custom logo
Should not have
• boring, traditional

```html
<!DOCTYPE html>
<html lang="en">
<head>
<meta charset="utf-8">
<title>Corvane Ventures — Business Card</title>
<link rel="stylesheet" href="https://fonts.googleapis.com/css2?family=Quicksand:wght@400;500&family=EB+Garamond:ital@1&display=swap">
<style>
  :root {
    --backdrop: #ececec;
    --card: #ffffff;
    --accent: #e0662a;
    --ink: #3a3a3a;
    --muted: #8a8a8a;
  }
  * { margin: 0; padding: 0; box-sizing: border-box; }
  html, body { width: 1200px; height: 952px; overflow: hidden; }
  body {
    background: var(--backdrop);
    font-family: "Quicksand", "Helvetica Neue", Arial, sans-serif;
    color: var(--ink);
    display: flex;
    align-items: center;
    justify-content: center;
    gap: 48px;
  }
  .card {
    width: 504px;
    height: 288px;
    background: var(--card);
    box-shadow: 0 2px 10px rgba(0,0,0,0.08);
    position: relative;
  }

  /* Front */
  .card--front {
    display: flex;
    flex-direction: column;
    justify-content: center;
    padding: 0 58px;
  }
  .brand__name {
    font-weight: 500;
    font-size: 50px;
    line-height: 1;
    letter-spacing: 6px;
    text-transform: uppercase;
    color: var(--ink);
  }
  .services {
    margin-top: 16px;
    font-size: 13px;
    font-weight: 500;
    letter-spacing: 0.4px;
    color: var(--ink);
  }
  .services__sep { color: var(--accent); margin: 0 4px; }
  .tagline {
    margin-top: 8px;
    font-family: "EB Garamond", Georgia, serif;
    font-style: italic;
    font-size: 15px;
    color: var(--muted);
  }

  /* Back */
  .card--back {
    display: flex;
    flex-direction: column;
    align-items: center;
    justify-content: center;
    text-align: center;
  }
  .contact__email {
    font-size: 21px;
    font-weight: 400;
    color: var(--accent);
  }
  .contact__rule {
    width: 330px;
    height: 1px;
    background: var(--accent);
    margin: 5px 0 6px;
  }
  .contact__role { font-size: 14px; font-weight: 500; color: var(--ink); }
  .contact__lines { margin-top: 14px; font-size: 17px; font-weight: 500; line-height: 1.35; }
  .contact__label { color: var(--accent); }
</style>
</head>
<body>
  <section class="card card--front" aria-label="Card front">
    <p class="brand__name">Corvane</p>
    <p class="services">consulting<span class="services__sep">•</span>software<span class="services__sep">•</span>building</p>
    <p class="tagline">built with clear intent</p>
  </section>

  <section class="card card--back" aria-label="Card back">
    <p class="contact__email">owen@corvane.ventures</p>
    <div class="contact__rule"></div>
    <p class="contact__role">client ambassador</p>
    <div class="contact__lines">
      <p><span class="contact__label">M.</span> +61 0455 219 604</p>
      <p><span class="contact__label">PO BOX</span> 418 Perth 6031</p>
    </div>
  </section>
</body>
</html>
```